Business Card for Polygraph business in Africa

Business Card . Polygraph Examiner based in Tanzania, East Africa.
Business Card will be used to disseminate contact information to potential clients.
It should convey that I am a professional specifically in the polygraph field and perform my work with integrity.

I have attached the business card that I'm currently using, which I threw together myself initially. It's not professional enough.

Target Market(s)

Banks, Accounting Firms, Government Ministries, Gas, Oil, & Gemstone Mining Concerns, Wildlife Conservation NGOs, International companies located in East Africa.

Industry/Entity Type

Business

Contact Information for Business Card

Veritrace Kilonga
Miriam Holloway
PO Box 48317
Arusha, Tanzania
+255 612 839 274
miriamholloway@postvale.example

Colors
00a990
f37122
faa54b

Requirements
Must have
• - Veritrace Kilonga (with the word "Polygraph" being more prominent than the word "Tanzania")
• - Forensic Examinations
• - Employment Screening
• - Should contain a logo of the Continental Truthline Society (of which I'm a member)
• - I would like an accent design (such as the polygraph "squiggles" of a cardio tracing or such as that)
• - My contact information (less prominent, but large enough to read legibly). I would also consider putting the contact information on the second side of the card.
Nice to have
• My color suggestions are changeable.
Should not have
• Anything "cutesy" or "cartoonish"

```html
<!DOCTYPE html>
<html lang="en">
<head>
<meta charset="utf-8">
<title>Veritrace Kilonga – Business Card</title>
<link href="https://fonts.googleapis.com/css2?family=Roboto:wght@400;500;700&family=Roboto+Condensed:wght@400;700&display=swap" rel="stylesheet">
<style>
  :root {
    --brand-blue: #0b4fa3;
    --brand-blue-deep: #084190;
    --ink-grey: #555a60;
    --muted-grey: #7a7f86;
    --card-white: #f7f7f6;
    --stage: #e4e2de;
    --seal-ring: #5a4fb0;
  }
  * { margin: 0; padding: 0; box-sizing: border-box; }
  html, body { width: 1200px; height: 911px; overflow: hidden; }
  body {
    background: var(--stage);
    font-family: "Roboto", Arial, sans-serif;
    position: relative;
  }
  .card {
    position: absolute;
    width: 560px;
    height: 320px;
    border-radius: 22px;
    overflow: hidden;
    box-shadow: 0 6px 18px rgba(0,0,0,.18);
  }
  /* Front side */
  .card-front { left: 70px; top: 110px; background: var(--card-white); }
  .corner-dot {
    position: absolute; right: -34px; top: -34px;
    width: 68px; height: 68px; border-radius: 50%;
    background: var(--brand-blue);
  }
  .holder {
    position: absolute; right: 108px; top: 40px; text-align: right;
  }
  .holder-name {
    font-family: "Roboto Condensed", Arial Narrow, sans-serif;
    font-weight: 700; font-size: 22px; color: var(--brand-blue);
    letter-spacing: .5px; text-transform: uppercase;
  }
  .holder-company {
    font-family: "Roboto Condensed", Arial Narrow, sans-serif;
    font-size: 14px; color: var(--muted-grey);
    text-transform: uppercase; letter-spacing: .5px; margin-top: 2px;
  }
  .member-seal { position: absolute; right: 30px; top: 32px; }
  .brand {
    position: absolute; left: 38px; top: 138px;
    display: flex; align-items: center; gap: 12px;
  }
  .brand-dot {
    width: 44px; height: 44px; border-radius: 50%;
    background: var(--brand-blue); flex: none;
  }
  .brand-name { font-weight: 700; font-size: 34px; color: var(--brand-blue); line-height: 1; }
  .brand-sub {
    font-weight: 700; font-size: 16px; color: var(--brand-blue);
    letter-spacing: 5px; margin-top: 4px;
  }
  .contact {
    position: absolute; left: 38px; bottom: 26px;
    font-size: 14px; color: var(--ink-grey); line-height: 1.45;
  }
  .contact-row { display: flex; align-items: center; gap: 8px; }
  .contact-row svg { width: 12px; height: 12px; flex: none; }
  .contact-plain { padding-left: 0; }

  /* Back side */
  .card-back {
    left: 570px; top: 480px;
    background: linear-gradient(160deg, var(--brand-blue) 0%, var(--brand-blue-deep) 100%);
    color: #fff;
  }
  .back-mark {
    position: absolute; left: 50%; top: 50%;
    transform: translate(-50%, -50%);
    display: flex; flex-direction: column; align-items: center; gap: 12px;
  }
  .back-mark-dot {
    width: 110px; height: 110px; border-radius: 50%;
    border: 8px solid #fff;
  }
  .back-mark-name { font-weight: 700; font-size: 20px; letter-spacing: .5px; }
  .services {
    position: absolute; left: 36px; top: 22px;
    writing-mode: vertical-rl;
    font-size: 15px; letter-spacing: .3px;
  }
  .services .sep { margin: 6px 0; }
</style>
</head>
<body>

  <section class="card card-front" aria-label="Business card front">
    <span class="corner-dot"></span>

    <div class="holder">
      <div class="holder-name">Miriam Holloway</div>
      <div class="holder-company">Veritrace Kilonga</div>
    </div>

    <svg class="member-seal" width="62" height="62" viewBox="0 0 62 62" role="img" aria-label="Continental Truthline Society membership seal">
      <circle cx="31" cy="31" r="29" fill="none" stroke="var(--seal-ring)" stroke-width="3"/>
      <circle cx="31" cy="31" r="20" fill="none" stroke="var(--seal-ring)" stroke-width="1.5"/>
    </svg>

    <div class="brand">
      <span class="brand-dot"></span>
      <div>
        <div class="brand-name">Veritrace</div>
        <div class="brand-sub">Kilonga</div>
      </div>
    </div>

    <div class="contact">
      <div class="contact-plain">PO Box 48317</div>
      <div class="contact-plain">Arusha, Tanzania</div>
      <div class="contact-row">
        <svg viewBox="0 0 12 12" aria-hidden="true"><path d="M3 1 L5 3.5 L4 5 Q5 7 7 8 L8.5 7 L11 9 L9.5 11 Q4 10 1 3 Z" fill="var(--brand-blue)"/></svg>
        <span>+255 612 839 274</span>
      </div>
      <div class="contact-row">
        <svg viewBox="0 0 12 12" aria-hidden="true"><rect x="1" y="2.5" width="10" height="7" rx="1" fill="var(--brand-blue)"/><path d="M1.5 3 L6 6.5 L10.5 3" fill="none" stroke="#fff" stroke-width="1"/></svg>
        <span>miriamholloway@postvale.example</span>
      </div>
      <div class="contact-row">
        <svg viewBox="0 0 12 12" aria-hidden="true"><circle cx="6" cy="6" r="5" fill="var(--brand-blue)"/><path d="M1 6 H11 M6 1 Q3 6 6 11 Q9 6 6 1" fill="none" stroke="#fff" stroke-width=".8"/></svg>
        <span>www.miriamholloway.example</span>
      </div>
    </div>
  </section>

  <section class="card card-back" aria-label="Business card back">
    <div class="services">
      <span>Forensic Examinations</span><span class="sep">•</span><span>Employment Screening</span>
    </div>
    <div class="back-mark">
      <span class="back-mark-dot"></span>
      <span class="back-mark-name">Veritrace Kilonga</span>
    </div>
  </section>

</body>
</html>
```